Laboratory and geotechnical service provider needs Word template

We require a new Word Template for our business. We are looking for a modern, business-like format. We typically generate reports such as management plans, business plans, method statements, technical reports. These reports cover generally between 5 and 30 pages, but sometimes up to 500 pages including the appendices.

Lab reports have their own formats and are not parts of this scope.

Target Market(s)

We report to Clients such as construction industry contractors, governmental departments and engineering consultants.

Industry/Entity Type

Technical Service

Colors

Designer to choose colors to be used in the design.

Requirements
Must have
• The report needs a fancy cover page with a title field, subtitle, project field, client name field, reference number field. Photo/graphics as background on cover. Second page needs a revision table for document control. Table of contents up to 2 levels. Appendices to be part of TOC. Report first page with custom headings for body text, titles, subtitles, headings 1, 2, 3, etc. Include a table with caption, figure with caption, bullet list, numbered list. Appendix page. Please use fonts consistently, choose a common, but professional, modern font.
Nice to have
• We traditionally use black and yellow as company colours. Please visit our company page www.brennixtesting.com.
Should not have
• The two attached word documents is what we use now for your information, we are looking for something better!

```html
<!DOCTYPE html>
<html lang="en">
<head>
<meta charset="UTF-8">
<title>Introduction – Stakeholder Management Plan</title>
<link href="https://fonts.googleapis.com/css2?family=Anton&family=Arimo:wght@400&family=Carlito:wght@700&display=swap" rel="stylesheet">
<style>
  :root {
    --brand-yellow: #fcec0c;
    --ink: #1a1a1a;
    --paper: #ffffff;
    --photo-light: #9a9a9a;
    --photo-mid: #6e6e6e;
    --photo-dark: #3c3c3c;
  }
  * { margin: 0; padding: 0; box-sizing: border-box; }
  html, body {
    width: 927px;
    height: 1200px;
    overflow: hidden;
    background: var(--paper);
  }
  .page {
    position: relative;
    width: 927px;
    height: 1200px;
    background: var(--paper);
    overflow: hidden;
  }
  .hero-photo {
    position: absolute;
    left: 0;
    top: 0;
    width: 927px;
    height: 540px;
    background:
      radial-gradient(ellipse at 78% 30%, #c9c9c9 0%, rgba(201,201,201,0) 45%),
      radial-gradient(ellipse at 30% 60%, var(--photo-light) 0%, rgba(154,154,154,0) 55%),
      linear-gradient(160deg, var(--photo-mid) 0%, #858585 45%, var(--photo-dark) 100%);
  }
  .section-frame {
    position: absolute;
    left: 87px;
    top: 406px;
    width: 775px;
    height: 710px;
    border: 5px solid var(--brand-yellow);
    border-radius: 3px;
  }
  .section-title {
    position: absolute;
    left: 0;
    right: 0;
    top: 444px;
    text-align: center;
    padding-left: 6px;
    font-family: "Anton", "Oswald", sans-serif;
    font-size: 60px;
    line-height: 1;
    letter-spacing: -0.5px;
    color: var(--brand-yellow);
  }
  .intro-copy {
    position: absolute;
    left: 154px;
    top: 584px;
    width: 660px;
    font-family: "Arimo", Arial, sans-serif;
    font-size: 16.4px;
    line-height: 24px;
    color: var(--ink);
  }
  .intro-copy span { display: block; white-space: nowrap; }
  .doc-ref {
    position: absolute;
    right: 28px;
    top: 1153px;
    font-family: "Carlito", Calibri, sans-serif;
    font-weight: 700;
    font-size: 12.5px;
    color: var(--ink);
    letter-spacing: 0.2px;
  }
</style>
</head>
<body>
  <main class="page">
    <div class="hero-photo" role="img" aria-label="Black and white photo of a laboratory technician in mask and lab coat working at a bench with pipettes, a microscope and sample tubes"></div>

    <div class="section-frame"></div>

    <h1 class="section-title">INTRODUCTION</h1>

    <div class="intro-copy">
      <span>The purpose of this Stakeholder Management Plan is to define the requirements,</span>
      <span>processes, and</span>
      <span>techniques for engaging stakeholders based on an analysis of their needs,</span>
      <span>interests, and abilities to</span>
      <span>impact the project.</span>
      <span>The objectives of the Stakeholder Management Plan are to document and</span>
      <span>communicate how</span>
      <span>information will be disseminated to, and received from all stakeholders connected</span>
      <span>with the project.</span>
      <span>The SMP shall therefore:</span>
      <span>• Identify who the stakeholders are</span>
      <span>• Establish the requirements of each stakeholder</span>
      <span>• The requirements of the project to receive information and/or obtain approvals</span>
      <span>from</span>
      <span>stakeholders</span>
      <span>• Analyse the power and interest of each stakeholder</span>
      <span>• Define the means and frequency of communication with each stakeholder</span>
    </div>

    <div class="doc-ref">DOC. # BT-O78097-SMP</div>
  </main>
</body>
</html>
```